Agriculture farming Hemp and CBD

The logo is in works with your company now, should be ready in a few days. We have our Domain (kestrelbrookhollow.com) We would like to see incorporated seed to growth, but not necessary. we would like to nature colors and some black and green. we have our farm and will be growing and selling HEMP and CBD we are based in the state of Virginia. Would like to incorporate the words pause, play, rewind if possible but not necessary.

Target Market(s)

20 years old to elderly

Coding

Coded - Design and coding required

Number of Pages Required

3 page

Font styles to use
Serif

Requirements
Must have
• I'm not sure on the must haves, we are open to any ideas, we would definitely like to see Hemp and CBD included, may the life cycle of seed to plant. We must have a pop up asking if you are 20 years old before they can enter our site and to view or purchase our product. I want the design to be totally different than what i uploaded.
Nice to have
• Would like to see natural colors as well as black and green
Should not have
• I want

```html
<!DOCTYPE html>
<html lang="en">
<head>
<meta charset="utf-8">
<title>Kestrel Brook Hollow — Hemp &amp; CBD</title>
<link rel="stylesheet" href="https://fonts.googleapis.com/css2?family=Montserrat:wght@400;500;600;700;800&family=Open+Sans:wght@400;600&display=swap">
<style>
:root{
  --black:#000;
  --green:#3aa51f;
  --green-dark:#1e8a12;
  --green-mid:#2f9a1a;
  --green-pale:#b9f0a4;
  --brown:#5c320c;
  --brown-dark:#4a2708;
  --grey-bg:#f4f4f4;
  --text:#111;
  --muted:#8a8a8a;
  --line:#d9d9d9;
  --cream:#f1dfb6;
}
*{margin:0;padding:0;box-sizing:border-box}
html,body{width:1200px;height:5164px;overflow:hidden}
body{position:relative;background:#fff;font-family:"Open Sans",Arial,sans-serif;color:var(--text)}
.abs{position:absolute}
h1,h2,h3,.mont{font-family:Montserrat,Arial,sans-serif}

/* header */
.site-header{left:0;top:0;width:1200px;height:90px;background:var(--black)}
.brand{left:92px;top:18px;display:flex;align-items:center;gap:12px;color:#fff;font-family:Montserrat,sans-serif;font-weight:600;font-size:15px;letter-spacing:1px}
.brand-dot{width:50px;height:50px;border:3px solid #fff;border-radius:50%}
.main-nav{right:78px;top:36px;display:flex;gap:40px;font-family:Montserrat,sans-serif;font-size:11.5px;color:#fff}
.main-nav .active{color:var(--green)}

/* hero */
.hero-photo{left:0;top:90px;width:1200px;height:690px;background:radial-gradient(ellipse at 65% 45%,#8a7a2a 0%,#5a4a1a 30%,#2a2410 65%,#141108 100%)}
.hero-disc{left:106px;top:185px;width:386px;height:386px;border-radius:50%;background:var(--green);text-align:center;color:#fff;padding-top:95px}
.hero-disc .kicker{font-family:Montserrat,sans-serif;font-size:27px;font-weight:500}
.hero-disc h1{font-size:43px;font-weight:800;line-height:52px;margin-top:6px}
.btn-brown{display:inline-block;background:var(--brown);color:#fff;font-family:Montserrat,sans-serif;font-weight:700;font-size:13px;border-radius:24px;padding:14px 38px;margin-top:20px}
.slider-dots{left:574px;top:666px;display:flex;gap:16px}
.slider-dots span{width:12px;height:12px;border-radius:50%;border:2px solid #fff}
.slider-dots span.on{background:#fff}
.hero-wave{left:0;top:690px}

/* badges */
.badge{width:240px;text-align:center}
.badge-ring{width:146px;height:146px;margin:0 auto;border:3px solid var(--green);border-radius:50%;position:relative}
.badge-ring::after{content:"";position:absolute;inset:14px;border:1.5px solid var(--green);border-radius:50%}
.badge-label{font-family:Montserrat,sans-serif;font-size:13px;font-weight:500;line-height:16px;margin-top:24px}

/* about */
.about-kicker{left:155px;top:1170px;font-family:Montserrat,sans-serif;font-size:23px;color:var(--green-dark)}
.about-title{left:155px;top:1200px;font-size:30px;font-weight:700}
.underline{height:3px;background:var(--green)}
.about-item{left:138px;width:500px;display:flex;gap:22px}
.about-icon{flex:none;width:90px;height:90px;border-radius:50%;border:4px solid #1a1a1a;border-top-color:var(--green);border-right-color:var(--green)}
.about-item h3{font-size:20px;font-weight:600;color:var(--green-dark);margin-top:4px}
.about-item p{font-size:11px;line-height:20px;color:var(--muted);margin-top:8px}
.about-illustration{left:680px;top:1130px;width:400px;height:440px;border-radius:50%;background:radial-gradient(circle,#e7a7a0 0%,#7aa86a 38%,#f4f4f4 60%,#fff 75%)}

/* featured */
.featured{left:0;top:1668px;width:1200px;height:665px;background:var(--grey-bg)}
.section-title{width:1200px;left:0;text-align:center;font-family:Montserrat,sans-serif;font-weight:700;font-size:24px}
.product{width:200px;text-align:center}
.product-img{width:150px;height:210px;margin:0 auto;border-radius:10px;background:linear-gradient(180deg,#e4e4e4,#b89a6a 60%,#5c3a14)}
.product-name{font-size:18px;color:#444;margin-top:32px}
.product-price{font-size:16px;color:#333;margin-top:2px}
.btn-green{display:inline-block;background:var(--green);color:#fff;font-family:Montserrat,sans-serif;font-weight:700;font-size:9px;border-radius:18px;padding:10px 28px;margin-top:10px}
.arrow{width:40px;height:70px}

/* cannabinoids */
.tile{width:306px;height:120px;background:var(--green-pale);display:flex;align-items:center;justify-content:center;font-family:Montserrat,sans-serif;font-weight:800;font-size:24px;color:#fff}
.tile.active{background:var(--green)}

/* testimonials */
.testimonials{left:0;top:2830px;width:1200px;height:535px;background:linear-gradient(90deg,var(--green),var(--green-dark))}
.t-card{width:312px;height:312px;border-radius:50%;border:3px solid #7fd263;padding:10px}
.t-inner{width:100%;height:100%;border-radius:50%;background:var(--green-mid);color:#fff;text-align:center;padding:40px 38px 0}
.t-inner.brown{background:var(--brown)}
.t-quote{font-family:Georgia,serif;font-size:60px;line-height:40px;opacity:.5}
.t-inner p{font-style:italic;font-size:11px;line-height:21px;margin-top:10px}
.t-name{font-weight:700;font-size:12px;margin-top:12px}
.stars{color:#ffd23a;font-size:17px;letter-spacing:2px}
.t-arrow{width:28px;height:28px;border-radius:50%;background:#fff;color:var(--green);text-align:center;line-height:26px;font-size:16px}

/* extracts */
.accordion{left:143px;top:3508px;width:912px;height:547px;border:1px solid var(--line)}
.acc-head{height:48px;border-bottom:1px solid var(--line);display:flex;justify-content:space-between;align-items:center;padding:0 46px;font-family:Montserrat,sans-serif;font-size:13px;color:#555}
.acc-head.open{color:var(--green-dark)}
.acc-panel{height:252px;border-bottom:1px solid var(--line);position:relative}
.acc-row{height:40px;border-bottom:1px solid var(--line);display:flex;justify-content:space-between;align-items:center;padding:0 30px;font-family:Montserrat,sans-serif;font-size:13px;color:#444}
.chev{width:10px;height:10px;border-right:1.5px solid #999;border-bottom:1.5px solid #999;transform:rotate(45deg)}
.chev.up{transform:rotate(-135deg)}
.seal{left:45px;top:25px;width:150px;height:150px;border-radius:50%;border:10px solid var(--green);background:#fff}
.seal-codes{left:50px;top:182px;font-family:Montserrat,sans-serif;font-weight:600;font-size:13px;line-height:18px;color:var(--green)}
.btn-small{display:inline-block;font-family:Montserrat,sans-serif;font-weight:700;font-size:8px;color:#fff;border-radius:14px;padding:9px 22px}
.plant-img{right:0;top:18px;width:360px;height:232px;background:radial-gradient(ellipse at 65% 55%,#6fa53a,#a9cd6a 40%,#fff 75%)}

/* contact */
.contact{left:0;top:4135px;width:1200px;height:640px;background:var(--brown)}
.field-photo{left:0;top:0;width:620px;height:640px;background:linear-gradient(90deg,#8a6a2a 0%,#5e6e22 45%,var(--brown) 100%)}
.contact h2{left:636px;top:102px;font-size:28px;font-weight:700;color:#fff}
.field{left:640px;width:428px;height:43px;background:#fff;font-size:13px;color:#555;padding:13px 18px}
.btn-send{left:638px;top:440px;width:140px;height:40px;border-radius:22px;background:var(--cream);color:var(--brown);font-family:Montserrat,sans-serif;font-weight:700;font-size:13px;text-align:center;line-height:40px}

/* footer */
.footer{left:0;top:4770px;width:1200px;height:394px;background:var(--black);color:#fff}
.footer-brand{left:122px;top:50px;font-family:Montserrat,sans-serif;font-weight:600;font-size:16px;display:flex;align-items:center;gap:10px}
.footer-brand .brand-dot{width:36px;height:36px}
.contact-list{left:122px;top:120px;font-size:12px;line-height:17px}
.contact-list div{display:flex;gap:10px;margin-bottom:14px}
.ico{width:14px;flex:none;color:var(--green)}
.f-col h4{font-family:Montserrat,sans-serif;font-weight:500;font-size:16px;margin-bottom:12px}
.f-col a{display:block;color:#fff;text-decoration:none;font-size:10px;line-height:29px}
.nl-input{width:238px;height:36px;background:#e8e8e8;color:#888;font-size:10px;padding:11px 14px}
.socials{display:flex;gap:10px}
.socials span{width:30px;height:30px;border-radius:50%;background:var(--green)}
.socials span.alt{background:var(--cream)}
.footer-rule{left:102px;top:302px;width:1012px;height:1px;background:#333}
.legal{top:330px;font-size:10px;color:#ccc}
</style>
</head>
<body>

<header class="site-header abs">
  <div class="brand abs"><span class="brand-dot"></span>KESTREL BROOK HOLLOW</div>
  <nav class="main-nav abs">
    <span class="active">HOME</span><span>ABOUT US</span><span>PRODUCTS</span><span>SHOP</span><span>BLOGS</span><span>TESTIMONIALS</span><span>CONTACT</span>
  </nav>
</header>

<section>
  <div class="hero-photo abs" role="img" aria-label="Close-up photograph of dried hemp flower buds"></div>
  <div class="hero-disc abs">
    <div class="kicker">Specialize in</div>
    <h1>Selling Quality<br>Hemp &amp; CBD</h1>
    <span class="btn-brown">CONTACT US ›</span>
  </div>
  <div class="slider-dots abs"><span class="on"></span><span></span><span></span></div>
  <svg class="hero-wave abs" width="1200" height="110" viewBox="0 0 1200 110">
    <path d="M0 20 C250 90 500 95 750 50 C950 15 1100 5 1200 40 L1200 110 L0 110Z" fill="#fff"/>
    <path d="M0 20 C250 80 500 80 750 40 C950 10 1100 0 1200 40 L1200 60 C1100 25 950 35 750 68 C500 108 250 100 0 48Z" fill="var(--green)"/>
    <path d="M0 52 C250 105 500 110 760 72 C950 45 1100 40 1200 62 L1200 72 C1100 52 950 58 760 86 C500 120 250 112 0 72Z" fill="var(--brown)"/>
  </svg>
</section>

<section>
  <div class="badge abs" style="left:107px;top:842px"><div class="badge-ring"></div><div class="badge-label">AMERICAN<br>MADE</div></div>
  <div class="badge abs" style="left:353px;top:842px"><div class="badge-ring"></div><div class="badge-label">FARM BILL<br>COMPLIANT</div></div>
  <div class="badge abs" style="left:597px;top:842px"><div class="badge-ring"></div><div class="badge-label">MADE WITH<br>INDUSTRIAL HEMP</div></div>
  <div class="badge abs" style="left:842px;top:842px"><div class="badge-ring"></div><div class="badge-label">PURITY THROUGH<br>INNOVATION</div></div>
</section>

<section>
  <div class="about-kicker abs">WELCOME</div>
  <h2 class="about-title abs">ABOUT KESTREL BROOK HOLLOW</h2>
  <div class="underline abs" style="left:155px;top:1252px;width:66px"></div>
  <div class="about-item abs" style="top:1300px">
    <div class="about-icon"></div>
    <div><h3>Who We Are</h3><p>Curabitur vel dolor ultrices ipsum dictum tristique Praesent vitae lacus Ut velit enim vestibulum non fermentum nec hendrerit quis leo Pellen-tesque rutrum malesuada neque Nunc tempus</p></div>
  </div>
  <div class="about-item abs" style="top:1441px">
    <div class="about-icon"></div>
    <div><h3>Our Vision</h3><p>Curabitur vel dolor ultrices ipsum dictum tristique Praesent vitae lacus Ut velit enim vestibulum non fermentum nec hendrerit quis leo Pellen-tesque rutrum malesuada neque Nunc tempus</p></div>
  </div>
  <div class="about-illustration abs" role="img" aria-label="Illustration of the hemp life cycle from seed to potted plant circling a central emblem"></div>
</section>

<section class="featured abs">
  <h2 class="section-title abs" style="top:60px">FEATURED PRODUCTS</h2>
  <svg class="arrow abs" style="left:92px;top:300px" viewBox="0 0 40 70"><path d="M34 4 L6 35 L34 66" fill="none" stroke="#777" stroke-width="2"/></svg>
  <svg class="arrow abs" style="left:1094px;top:300px" viewBox="0 0 40 70"><path d="M6 4 L34 35 L6 66" fill="none" stroke="#777" stroke-width="2"/></svg>
  <div class="product abs" style="left:144px;top:170px"><div class="product-img" role="img" aria-label="CBD oil dropper bottle"></div><div class="product-name">CBD Product</div><div class="product-price">$49.99</div><span class="btn-green">SHOP NOW ›</span></div>
  <div class="product abs" style="left:383px;top:170px"><div class="product-img" role="img" aria-label="CBD vape pen"></div><div class="product-name">CBD Product</div><div class="product-price">$49.99</div><span class="btn-green">SHOP NOW ›</span></div>
  <div class="product abs" style="left:622px;top:170px"><div class="product-img" role="img" aria-label="CBN and CBD tincture bottle"></div><div class="product-name">CBD Product</div><div class="product-price">$49.99</div><span class="btn-green">SHOP NOW ›</span></div>
  <div class="product abs" style="left:861px;top:170px"><div class="product-img" role="img" aria-label="CBD vaporizer with hemp flower"></div><div class="product-name">CBD Product</div><div class="product-price">$49.99</div><span class="btn-green">SHOP NOW ›</span></div>
</section>

<section>
  <h2 class="section-title abs" style="top:2394px">SHOP BY CANNABINOIDS</h2>
  <div class="underline abs" style="left:570px;top:2432px;width:60px"></div>
  <div class="tile abs" style="left:112px;top:2477px">CBC</div>
  <div class="tile active abs" style="left:438px;top:2477px">CBD</div>
  <div class="tile abs" style="left:770px;top:2477px">CBG</div>
  <div class="tile abs" style="left:112px;top:2617px">CBN</div>
  <div class="tile abs" style="left:440px;top:2617px">DELTA 8 THC</div>
  <div class="tile abs" style="left:772px;top:2617px">THCV</div>
</section>

<section class="testimonials abs">
  <h2 class="section-title abs" style="top:54px;color:#fff;font-size:28px">TESTIMONIALS</h2>
  <div class="underline abs" style="left:570px;top:100px;width:60px;background:#fff"></div>
  <div class="t-arrow abs" style="left:84px;top:270px">‹</div>
  <div class="t-arrow abs" style="left:1122px;top:270px">›</div>
  <div class="t-card abs" style="left:126px;top:142px"><div class="t-inner"><div class="t-quote">“</div><p>Aultricies orci ac feugiat suscipit leo massa sodales velit et scelerisque mi tortor at ipsum Proin orci odio commodo ac gravida non tristique vel te Curabitur iaculis tempus eros</p><div class="t-name">Nora Lind</div><div class="stars">★★★★★</div></div></div>
  <div class="t-card abs" style="left:451px;top:142px"><div class="t-inner brown"><div class="t-quote">“</div><p>Aultricies orci ac feugiat suscipit leo massa sodales velit et scelerisque mi tortor at ipsum Proin orci odio commodo ac gravida non tristique vel te Curabitur iaculis tempus eros</p><div class="t-name">Nora Lind</div><div class="stars">★★★★★</div></div></div>
  <div class="t-card abs" style="left:771px;top:142px"><div class="t-inner"><div class="t-quote">“</div><p>Aultricies orci ac feugiat suscipit leo massa sodales velit et scelerisque mi tortor at ipsum Proin orci odio commodo ac gravida non tristique vel te Curabitur iaculis tempus eros</p><div class="t-name">Nora Lind</div><div class="stars">★★★★★</div></div></div>
</section>

<section>
  <h2 class="section-title abs" style="top:3428px">FOCUSED EXTRACTS</h2>
  <div class="underline abs" style="left:570px;top:3466px;width:60px"></div>
  <div class="accordion abs">
    <div class="acc-head open">NATURAL <span class="chev up"></span></div>
    <div class="acc-panel">
      <div class="seal abs"></div>
      <div class="seal-codes abs">CBD CBN CBDa<br>CBC CBG CBDv</div>
      <div class="abs" style="left:228px;top:50px;width:430px">
        <h3 style="font-size:17px;font-weight:600">Natural Broad Spectrum Blend</h3>
        <p style="font-size:11px;line-height:20px;color:var(--muted);margin-top:10px">Curabitur vel dolor ultrices ipsum dictum tristique Praesent vitae lacus Ut velit enim vestibulum non fermentum nec hendrerit quis leo</p>
        <div style="margin-top:16px;display:flex;gap:8px"><span class="btn-small" style="background:var(--green)">SHOP NOW ›</span><span class="btn-small" style="background:var(--brown)">SEE LAB TEST ›</span></div>
      </div>
      <div class="plant-img abs" role="img" aria-label="Photograph of a green hemp plant"></div>
    </div>
    <div class="acc-row">CALM <span class="chev"></span></div>
    <div class="acc-row">COMFORTABLY NUMB <span class="chev"></span></div>
    <div class="acc-row">FOCUS <span class="chev"></span></div>
    <div class="acc-row">HAPPY <span class="chev"></span></div>
    <div class="acc-row">SLEEP <span class="chev"></span></div>
    <div class="acc-row" style="border-bottom:0">SOOTHE <span class="chev"></span></div>
  </div>
</section>

<section class="contact abs">
  <div class="field-photo abs" role="img" aria-label="Photograph of a hemp field at sunset"></div>
  <h2 class="abs">GET IN TOUCH WITH US</h2>
  <div class="field abs" style="top:165px">Name*</div>
  <div class="field abs" style="top:220px">Email *</div>
  <div class="field abs" style="top:275px">Phone*</div>
  <div class="field abs" style="top:330px;height:80px">Message</div>
  <div class="btn-send abs">SEND ›</div>
  <svg class="abs" style="left:0;top:530px" width="1200" height="110" viewBox="0 0 1200 110">
    <path d="M0 60 C300 10 600 20 850 60 C1000 85 1120 70 1200 40 L1200 110 L0 110Z" fill="var(--cream)"/>
    <path d="M0 72 C300 25 600 35 850 75 C1000 98 1120 85 1200 55 L1200 110 L0 110Z" fill="var(--green)"/>
    <path d="M0 86 C300 45 600 55 850 92 C1000 110 1120 100 1200 75 L1200 110 L0 110Z" fill="var(--black)"/>
  </svg>
</section>

<footer class="footer abs">
  <div class="footer-brand abs"><span class="brand-dot"></span>KESTREL BROOK HOLLOW</div>
  <div class="contact-list abs">
    <div><svg class="ico" viewBox="0 0 14 18" height="16"><path d="M7 1a5.5 5.5 0 0 0-5.5 5.5C1.5 11 7 17 7 17s5.5-6 5.5-10.5A5.5 5.5 0 0 0 7 1z" fill="currentColor"/><circle cx="7" cy="6.5" r="2" fill="#000"/></svg><span>48 Millrace Lane, Floyd,<br>VA 24091</span></div>
    <div><svg class="ico" viewBox="0 0 14 14" height="14"><path d="M3 1l2.5 3-1.5 1.5a8 8 0 0 0 4.5 4.5L10 8.5l3 2.5-1.5 2C6 13 1 8 1 2.5z" fill="currentColor"/></svg><span>(540) 555-0182</span></div>
    <div><svg class="ico" viewBox="0 0 14 10" height="10"><rect x="0" y="0" width="14" height="10" fill="currentColor"/><path d="M0 0l7 5 7-5" fill="none" stroke="#000"/></svg><span>hello@kestrelbrookhollow.com</span></div>
  </div>
  <div class="f-col abs" style="left:456px;top:86px"><h4>Information</h4><a>About Us</a><a>Why Choose Us</a><a>Our Products</a><a>What People Says</a><a>Contact Us</a></div>
  <div class="f-col abs" style="left:670px;top:86px"><h4>Sitemap</h4><a>Our Blogs</a><a>Hemp Products</a><a>CBD Products</a><a>Term of Use</a><a>Contact Us</a></div>
  <div class="f-col abs" style="left:848px;top:86px"><h4>Join Our Newsletters</h4>
    <div class="nl-input">Your Email address</div>
    <span class="btn-small" style="background:var(--green);margin-top:10px;padding:9px 30px">SUBSCRIBE</span>
    <div class="socials" style="margin-top:16px"><span></span><span class="alt"></span><span class="alt"></span><span class="alt"></span></div>
  </div>
  <div class="footer-rule abs"></div>
  <div class="legal abs" style="left:102px">© Copyright 2020 . Kestrel Brook Hollow . All Right Reserved</div>
  <div class="legal abs" style="right:86px">Terms &amp; Conditions &nbsp;|&nbsp; Privacy Policy</div>
</footer>

</body>
</html>
```